LANTERN - and the quiet crafts of everyday life

I´m writing a book about CHANGE and the skills leaders needs to embody the transformation from being amanager to become leaders.
The title of the book in Icelandic is the same as the name of the project (which I want to be used on the designes is:) UPPSPRETTA
(with the subtitle:) og hugrekki hversdagsins

Change is not controlled or managed – Leading effective change is an art form which is one of the big reasons for why 70% of changes within companies fail. The main reason however, is that managers are tasked with managing and directing them. The art form of change is to put it in the hands of leaders who possess the emotional intelligence that is needed – all their other advantages intact – to lead change all the way.

The big problem when it comes to change is that there are too many managers and too few leaders within companies – leaders who possess emotional intelligence which is the most important skill a leader embodies to empower change. A leader has what it takes to empower followership.

A manager tends to push and control, make decisions that he presupposes others to implement the way he expects. An emotionally competent leader leads by example and enhances followership on that journey because of the trust and respect he has earned.

In few words: SOFT SKILLS ARE THE NEW HARD SKILLS!

```html
<!DOCTYPE html>
<html lang="is">
<head>
<meta charset="utf-8">
<title>Uppspretta – book cover spread</title>
<link rel="stylesheet" href="https://fonts.googleapis.com/css2?family=Roboto:ital,wght@0,400;0,700;0,900;1,400&family=Roboto+Condensed:wght@400;500&display=swap">
<style>
  :root {
    --canvas-bg: #d4d4d4;
    --paper: #ffffff;
    --title-red: #e43d2a;
    --ink: #1a1a1a;
    --body-ink: #222222;
    --placeholder: #dcdddf;
    --spine-line: #e9c9c4;
    --sky-top: #fdf3c4;
    --sky-mid: #f6c46a;
    --glow: #e47a2c;
    --rock: #6e2412;
    --rock-deep: #1e0906;
  }
  * { box-sizing: border-box; margin: 0; padding: 0; }
  html, body { width: 1200px; height: 1200px; overflow: hidden; }
  body {
    background: var(--canvas-bg);
    font-family: "Roboto", Arial, sans-serif;
    position: relative;
  }
  .spread {
    position: absolute;
    left: 40px; top: 325px;
    width: 1120px; height: 549px;
    display: flex;
  }
  .back-cover {
    position: relative;
    width: 528px; height: 100%;
    background: var(--paper);
  }
  .spine {
    position: relative;
    width: 63px; height: 100%;
    background: var(--paper);
    border-left: 1px solid var(--spine-line);
    border-right: 1px solid var(--spine-line);
  }
  .front-cover {
    position: relative;
    width: 529px; height: 100%;
    overflow: hidden;
  }

  /* back cover */
  .back-title {
    position: absolute; top: 38px; left: 0; width: 100%;
    text-align: center;
    font-weight: 900; font-size: 50px; letter-spacing: 0.5px;
    color: var(--title-red); line-height: 1;
  }
  .back-subtitle {
    position: absolute; top: 94px; left: 0; width: 100%;
    text-align: center;
    font-family: "Roboto Condensed", Arial, sans-serif;
    font-size: 18px; color: var(--ink);
  }
  .blurb {
    position: absolute; top: 138px; left: 57px; width: 413px;
    font-family: "Roboto Condensed", Arial, sans-serif;
    font-size: 9.6px; line-height: 13.4px; color: var(--body-ink);
    text-align: justify;
  }
  .divider {
    position: absolute; top: 327px; left: 160px; width: 205px; height: 1px;
    background: linear-gradient(90deg, transparent, var(--title-red) 20%, var(--title-red) 80%, transparent);
  }
  .author-photo {
    position: absolute; top: 349px; left: 57px; width: 75px; height: 90px;
    background: var(--placeholder);
  }
  .author-name {
    position: absolute; top: 352px; left: 145px;
    font-family: "Roboto Condensed", Arial, sans-serif;
    font-weight: 500; font-size: 16px; color: var(--ink);
  }
  .author-bio {
    position: absolute; top: 374px; left: 146px; width: 324px;
    font-family: "Roboto Condensed", Arial, sans-serif;
    font-size: 9.6px; line-height: 13.4px; color: var(--body-ink);
    text-align: justify;
  }

  /* spine */
  .spine-title, .spine-author {
    position: absolute; left: 50%;
    writing-mode: vertical-rl;
    transform: translateX(-50%);
    white-space: nowrap;
  }
  .spine-title {
    top: 38px;
    font-weight: 900; font-size: 24px; letter-spacing: 1px;
    color: var(--title-red);
  }
  .spine-author {
    top: 362px;
    font-family: "Roboto Condensed", Arial, sans-serif;
    font-weight: 500; font-size: 15px; letter-spacing: 1px;
    color: var(--ink);
  }

  /* front cover */
  .cover-art {
    position: absolute; inset: 0;
    background:
      radial-gradient(ellipse 60% 30% at 45% 55%, rgba(255,220,150,0.55), transparent 70%),
      linear-gradient(180deg, var(--sky-top) 0%, var(--sky-top) 16%, var(--sky-mid) 40%, var(--glow) 58%, var(--rock) 75%, var(--rock-deep) 100%);
  }
  .front-title {
    position: absolute; top: 56px; left: 0; width: 100%;
    text-align: center;
    font-weight: 900; font-size: 58px; letter-spacing: 0.5px;
    color: var(--title-red); line-height: 1;
  }
  .front-subtitle {
    position: absolute; top: 137px; left: 0; width: 100%;
    text-align: center;
    font-style: italic; font-size: 22px; color: var(--ink);
  }
  .front-author {
    position: absolute; top: 476px; left: 384px;
    font-family: "Roboto Condensed", Arial, sans-serif;
    font-weight: 500; font-size: 21px; line-height: 25px; letter-spacing: 0.5px;
    color: #ffffff;
  }
</style>
</head>
<body>
  <div class="spread">
    <section class="back-cover">
      <h2 class="back-title">UPPSPRETTA</h2>
      <p class="back-subtitle">og hugrekki hversdagsins</p>
      <div class="blurb">
        <p>Lorem ipsum dolor sit amet, consectetuer adipiscing elit, sed diam nonummy nibh euismod tincidunt ut laoreet dolore magna aliquam erat volutpat. Ut wisi enim ad minim veniam, quis nostrud exerci tation ullamcorper suscipit lobortis nisl ut aliquip ex ea commodo consequat. Duis autem vel eum iriure dolor in hendrerit in vulputate velit esse molestie consequat, vel illum dolore eu feugiat nulla facilisis at vero eros et accumsan et iusto odio dignissim qui blandit praesent luptatum zzril delenit augue duis dolore te feugait nulla facilisi.</p>
        <p>Lorem ipsum dolor sit amet, cons ectetuer adipiscing elit, sed diam nonummy nibh euismod tincidunt ut laoreet dolore magna aliquam erat volutpat. Ut wisi enim ad minim veniam, quis nostrud exerci tation ullamcorper suscipit lobortis nisl ut aliquip ex ea commodo consequat.</p>
        <p>Lorem ipsum dolor sit amet, consectetuer adipiscing elit, sed diam nonummy nibh euismod tincidunt ut laoreet dolore magna aliquam erat volutpat. Ut wisi enim ad minim veniam, quis nostrud exerci tation ullamcorper suscipit lobortis nisl ut aliquip ex ea commodo consequat. Duis autem vel eum iriure dolor in hendrerit</p>
      </div>
      <div class="divider"></div>
      <div class="author-photo" role="img" aria-label="Author portrait placeholder"></div>
      <h3 class="author-name">BALDUR ÞÓRSSON</h3>
      <p class="author-bio">Lorem ipsum dolor sit amet, consectetuer adipiscing elit, sed diam nonummy nibh euismod tincidunt ut laoreet dolore magna aliquam erat volutpat. Ut wisi enim ad minim veniam, quis nostrud exerci tation ullamcorper suscipit lobortis nisl ut aliquip ex ea commodo consequat. Duis autem vel eum iriure dolor in.</p>
    </section>

    <section class="spine">
      <span class="spine-title">UPPSPRETTA</span>
      <span class="spine-author">BALDUR ÞÓRSSON</span>
    </section>

    <section class="front-cover">
      <div class="cover-art" role="img" aria-label="Photograph of a figure leaping between two rocky cliffs over a mountain valley at sunset"></div>
      <h1 class="front-title">UPPSPRETTA</h1>
      <p class="front-subtitle">og hugrekki hversdagsins</p>
      <p class="front-author">BALDUR<br>ÞÓRSSON</p>
    </section>
  </div>
</body>
</html>
```